Website mockup using figma or other design software for Plumbing Company

We are looking for a talented UI/UX designer to create a high-converting, modern, and professional website design for a local plumbing company. The goal is to move away from the "dated" look of traditional trades and provide a seamless, trustworthy experience for homeowners and commercial clients.
The Challenge
Create a Homepage and a Service Page design that balances professional expertise with an urgent "call-to-action" (CTA) focus. We need a design that looks great on desktop but is built with a mobile-first mindset, as most customers find plumbers via their phones during emergencies.
This company will focus more on B2B, and corporate contracts, but should still be friendly to the public.
Here are some examples of what we are looking for
https://velotrin-works.com/construction/plumbing-construction/
https://velotrin-works.com/
The company is called "KT Plumbing."
Please see the logo below.

```html
<!DOCTYPE html>
<html lang="en">
<head>
<meta charset="utf-8">
<title>Velotrin – Commercial Plumbing</title>
<link href="https://fonts.googleapis.com/css2?family=Montserrat:wght@400;500;600;700;800&family=Lato:wght@400;700&family=Roboto:wght@500&display=swap" rel="stylesheet">
<style>
:root{
  --navy:#13202e;
  --navy-deep:#0f1b28;
  --teal:#0d3a4f;
  --ink:#1a1a1a;
  --body:#6b6b6b;
  --white:#ffffff;
  --line:#c9d1d8;
}
*{margin:0;padding:0;box-sizing:border-box}
html,body{width:1200px;height:3770px;overflow:hidden;background:var(--white)}
body{position:relative;font-family:'Lato',sans-serif;color:var(--ink)}
.abs{position:absolute}
.brand{display:flex;align-items:center;gap:10px;font-family:'Montserrat',sans-serif;font-weight:800;color:var(--navy);letter-spacing:-0.5px}
.brand-square{background:var(--navy);display:block}
.btn{position:absolute;display:flex;align-items:center;justify-content:center;font-family:'Lato',sans-serif;font-weight:700;clip-path:polygon(4% 0,100% 0,96% 100%,0 100%)}
.btn-dark{background:var(--navy);color:var(--white)}
.btn-light{background:var(--white);color:var(--navy)}

/* header */
.site-header{left:0;top:0;width:1200px;height:69px;background:var(--white)}
.nav a{position:absolute;top:24px;font-size:13px;color:#333;text-decoration:none;font-family:'Montserrat',sans-serif}
.nav a.active{font-weight:700;color:var(--ink)}
.nav-underline{left:419px;top:65px;width:46px;height:4px;background:var(--navy)}

/* hero */
.hero-photo{left:0;top:69px;width:1200px;height:604px;background:linear-gradient(90deg,#ecebe7 0%,#dcdad5 40%,#9aa0a3 62%,#6c6f66 80%,#8a8c7a 100%)}
.hero-title{left:110px;top:138px;font-family:'Montserrat',sans-serif;font-size:47px;line-height:61px;color:var(--navy);font-weight:500}
.hero-title b{font-weight:800}
.hero-text{left:109px;top:390px;width:400px;font-size:14px;line-height:28px;color:#222}

/* about */
.about-photo{left:111px;top:758px;width:448px;height:446px;background:linear-gradient(160deg,#8fa7b8 0%,#b6ab8e 45%,#a07c55 75%,#6d5a45 100%)}
.section-title{font-family:'Montserrat',sans-serif;font-size:42px;color:var(--navy);font-weight:400;display:flex;align-items:center;gap:12px}
.section-title b{font-weight:800}
.section-title .mark{width:30px;height:30px;background:var(--navy);display:block}
.about-text{left:648px;top:850px;width:442px;font-size:14px;line-height:31px;color:var(--body);text-align:justify}
.about-text p+p{margin-top:12px}

/* service band */
.band{left:0;top:1302px;width:1200px;height:552px;background:var(--white)}
.panel{position:absolute;top:0;height:552px}
.panel-mep{left:0;width:480px;background:linear-gradient(180deg,#c8c4bd 0%,#a6653f 45%,#6d3b26 75%,#1a1410 100%);clip-path:polygon(0 0,478px 0,319px 552px,0 552px)}
.panel-service{left:0;width:1200px;background:linear-gradient(180deg,#0a2d3f 0%,#0d3a4f 55%,#0b2a3a 100%);clip-path:polygon(485px 0,888px 0,783px 552px,326px 552px)}
.panel-comp{left:0;width:1200px;background:linear-gradient(180deg,#1f5fb0 0%,#7aa2d8 40%,#e8ecef 58%,#4d4d4a 82%,#1d1d1b 100%);clip-path:polygon(895px 0,1200px 0,1200px 552px,790px 552px)}
.panel-label{position:absolute;font-family:'Montserrat',sans-serif;font-weight:700;color:var(--white);font-size:32px}
.service-copy{left:440px;top:1488px;width:380px;text-align:center;color:var(--white)}
.service-copy h3{font-family:'Montserrat',sans-serif;font-weight:700;font-size:32px;margin-bottom:14px}
.service-copy p{font-size:15.5px;line-height:28px;font-weight:700}

/* values */
.value{position:absolute;top:2038px;width:230px}
.value-icon{width:64px;height:64px;border-radius:50%;background:var(--white);box-shadow:0 2px 8px rgba(0,0,0,.18);display:flex;align-items:center;justify-content:center}
.value-icon.active{background:var(--navy)}
.value-name{position:absolute;left:86px;top:20px;font-family:'Montserrat',sans-serif;font-size:20px;color:var(--ink)}
.value-text{margin-top:30px;font-size:12.5px;line-height:23.5px;color:var(--body)}

/* cta */
.cta{left:111px;top:2324px;width:978px;height:363px;border-radius:8px;background:linear-gradient(180deg,#2a2e33 0%,#5a1d1a 50%,#2b2222 100%)}
.cta h2{position:absolute;left:0;top:96px;width:100%;text-align:center;font-family:'Montserrat',sans-serif;font-weight:800;font-size:45px;color:var(--white)}
.cta p{position:absolute;left:0;top:168px;width:100%;text-align:center;font-weight:700;font-size:15.5px;color:var(--white)}

/* projects */
.project{position:absolute;border-radius:6px}
.project-caption{left:155px;top:3234px;font-family:'Roboto',sans-serif;font-weight:500;font-size:27px;color:var(--white)}

/* footer */
.site-footer{left:0;top:3391px;width:1200px;height:379px;background:var(--navy-deep);color:var(--white)}
.footer-col h4{font-family:'Lato',sans-serif;font-weight:700;font-size:19px;margin-bottom:10px}
.footer-col a{display:block;color:var(--white);text-decoration:none}
.quick a{font-size:13px;line-height:24px}
.other a{font-size:14.5px;line-height:30px}
.contact-row{position:absolute;left:913px;display:flex;gap:16px;font-size:15px;line-height:23px}
.social{position:absolute;top:3656px;width:32px;height:32px;border-radius:50%;background:var(--white)}
</style>
</head>
<body>

<header class="site-header abs">
  <div class="brand abs" style="left:112px;top:16px;font-size:27px">
    <span class="brand-square" style="width:34px;height:34px"></span>VELOTRIN
  </div>
  <nav class="nav">
    <a class="active" style="left:421px">Home</a>
    <a style="left:494px">VT Service</a>
    <a style="left:596px">VT MEP</a>
    <a style="left:683px">Projects</a>
    <a style="left:767px">Careers</a>
    <a style="left:849px">About</a>
    <a style="left:920px">Blog</a>
  </nav>
  <div class="nav-underline abs"></div>
  <a class="btn btn-dark" style="left:986px;top:10px;width:102px;height:41px;font-size:13px;font-family:'Montserrat',sans-serif">CONTACT</a>
</header>

<section>
  <div class="hero-photo abs" role="img" aria-label="Plumber in hard hat and safety vest tightening a chrome flush valve with a pipe wrench"></div>
  <h1 class="hero-title abs"><b>Commercial<br>Plumbing</b> Solutions<br>Built for Reliability &amp;<br>Scale</h1>
  <p class="hero-text abs">Serving contractors, property managers, and businesses with dependable plumbing installation, repair, and maintenance services.</p>
  <a class="btn btn-dark" style="left:112px;top:491px;width:202px;height:44px;font-size:13.5px">Request Service Call Now</a>
</section>

<section>
  <div class="about-photo abs" role="img" aria-label="Worker in orange shirt and hard hat drilling among underground pipe stubs on a job site"></div>
  <h2 class="section-title abs" style="left:644px;top:764px"><span class="mark"></span>About <b>Us</b></h2>
  <div class="about-text abs">
    <p>Velotrin is leading the evolution of construction. Each day we wake up and show up with a charge to fulfill our mission.</p>
    <p>Velotrin takes a big-picture approach to the construction process by self-performing electrical, HVAC, plumbing, process piping, underground utilities, prefabrication, and MEP design. Instead of multiple consultants and countless subcontractors, our customers work with just one company to eliminate profit layers, scope gaps, and complexity of schedules.</p>
  </div>
  <a class="btn btn-dark" style="left:644px;top:1135px;width:128px;height:43px;font-size:13px">READ MORE</a>
</section>

<section class="band abs">
  <div class="panel panel-mep" role="img" aria-label="Worker in orange shirt installing overhead copper piping"></div>
  <div class="panel panel-service" role="img" aria-label="Dark teal overlay of a technician at a service panel"></div>
  <div class="panel panel-comp" role="img" aria-label="Crane lifting a white prefabricated component module onto a truck"></div>
  <span class="panel-label" style="left:99px;top:476px">VT MEP</span>
  <span class="panel-label" style="left:870px;top:476px">VT COMPONENTS</span>
</section>
<div class="service-copy abs">
  <h3>VT SERVICE</h3>
  <p>VT Service offers a single point of contact for reliable service, maintenance, installations, and repairs across multiple trades.</p>
</div>
<a class="btn btn-light" style="left:549px;top:1659px;width:125px;height:43px;font-size:13px">READ MORE</a>

<section>
  <h2 class="section-title abs" style="left:446px;top:1940px"><span class="mark"></span>Our <b>Values</b></h2>

  <div class="value" style="left:111px">
    <div class="value-icon"><svg width="30" height="30" viewBox="0 0 30 30"><g fill="#1e2a38"><circle cx="15" cy="10" r="4.5"/><circle cx="7" cy="12" r="3.2"/><circle cx="23" cy="12" r="3.2"/><path d="M8 24c0-5 3-8 7-8s7 3 7 8z"/><path d="M1 23c0-4 2-6 5-6 1 0 2 .3 3 1-1.5 1.5-2 3-2 5z"/><path d="M29 23c0-4-2-6-5-6-1 0-2 .3-3 1 1.5 1.5 2 3 2 5z"/></g></svg></div>
    <span class="value-name">Teamwork</span>
    <p class="value-text">Our people are the root of our success. We prioritize team over individual and understand collaboration is key to our success.</p>
  </div>
  <div class="value" style="left:367px">
    <div class="value-icon"><svg width="32" height="32" viewBox="0 0 32 32"><circle cx="16" cy="16" r="11" fill="#1e2a38"/><path d="M11 16l3.5 3.5L21 13" stroke="#fff" stroke-width="2.5" fill="none"/></svg></div>
    <span class="value-name">Excellence</span>
    <p class="value-text">No matter what it is, from writing an email to installing equipment, we are committed to putting our whole hearts and minds into everything we do.</p>
  </div>
  <div class="value" style="left:623px">
    <div class="value-icon active"><svg width="30" height="30" viewBox="0 0 30 30"><path d="M4 24l7-10 5 6 4-5 6 9z" fill="#fff"/><circle cx="21" cy="8" r="3" fill="#fff"/></svg></div>
    <span class="value-name" style="top:22px">Perseverance</span>
    <p class="value-text">We have a never-give-up attitude. This comes from our willingness to problem-solve and our natural tendency to always look at the glass half full.</p>
  </div>
  <div class="value" style="left:879px">
    <div class="value-icon"><svg width="30" height="30" viewBox="0 0 30 30"><circle cx="15" cy="15" r="10" fill="none" stroke="#1e2a38" stroke-width="4" stroke-dasharray="4 2"/><circle cx="15" cy="15" r="4" fill="#1e2a38"/></svg></div>
    <span class="value-name">Integrity</span>
    <p class="value-text">We are individually and collectively accountable for our actions and expect honesty, openness, and transparency from our team.</p>
  </div>
</section>

<section class="cta abs" role="img" aria-label="Rows of prefabricated copper piping on red racks in a workshop">
  <h2>Need Reliable Plumbing Support?</h2>
  <p>Our team is ready to assist with installations, maintenance, or emergency repairs.</p>
</section>
<a class="btn btn-light" style="left:506px;top:2549px;width:186px;height:41px;font-size:13px">CALL EMERGENCY LINE</a>

<section>
  <h2 class="section-title abs" style="left:430px;top:2778px"><span class="mark"></span>Our <b>Projects</b></h2>
  <div class="project" style="left:111px;top:2874px;width:445px;height:417px;background:linear-gradient(180deg,#5f86b8 0%,#8ea07a 38%,#a48d6d 65%,#2e2a27 100%)" role="img" aria-label="Underground plumbing stubs and excavator on a construction site"></div>
  <span class="project-caption abs">Lorm Ipsum Dolor Siet</span>
  <div class="project" style="left:580px;top:2874px;width:217px;height:203px;background:linear-gradient(160deg,#c7532f 0%,#d48a5f 45%,#9aa0a4 100%)" role="img" aria-label="Worker fitting copper pipes in a ceiling space"></div>
  <div class="project" style="left:811px;top:2874px;width:278px;height:203px;background:linear-gradient(160deg,#d8d8d6 0%,#b88b6b 50%,#cf6a34 100%)" role="img" aria-label="Worker brazing copper pipe with a torch"></div>
  <div class="project" style="left:580px;top:3089px;width:278px;height:202px;background:linear-gradient(160deg,#6e7b53 0%,#8aa845 45%,#5a4b3d 100%)" role="img" aria-label="Worker in high-visibility shirt assembling pipe fittings"></div>
  <div class="project" style="left:871px;top:3089px;width:218px;height:202px;background:linear-gradient(90deg,#c8ccd0 0%,#b47a54 45%,#d6d9dc 100%)" role="img" aria-label="Copper pipe risers against a metal wall"></div>
</section>

<footer class="site-footer abs">
  <div class="brand abs" style="left:110px;top:76px;font-size:38px;color:var(--white)">
    <span class="brand-square" style="width:48px;height:48px;background:var(--white)"></span>VELOTRIN
  </div>
  <p class="abs" style="left:112px;top:162px;width:280px;font-size:14px;line-height:26px">Professional plumbing solutions for businesses, contractors, and property managers.</p>

  <div class="footer-col quick abs" style="left:530px;top:97px">
    <h4>Quick Links</h4>
    <a>Home</a><a>VT Service</a><a>VT MEP</a><a>Projects</a><a>Careers</a><a>About</a><a>Blog</a>
  </div>
  <div class="footer-col other abs" style="left:702px;top:97px">
    <h4>Other Links</h4>
    <a>Privacy Policy</a><a>Terms &amp; Conditions</a><a>Disclaimer</a><a>Support</a><a>Help</a>
  </div>
  <div class="footer-col abs" style="left:913px;top:97px"><h4>Contact Info</h4></div>

  <div class="contact-row" style="top:144px">
    <svg width="22" height="24" viewBox="0 0 22 24"><path d="M11 1a8 8 0 0 0-8 8c0 6 8 14 8 14s8-8 8-14a8 8 0 0 0-8-8z" fill="#fff"/><circle cx="11" cy="9" r="3" fill="#0f1b28"/></svg>
    <span>418 Cobalt Lane<br>Reno, NV 89502</span>
  </div>
  <div class="contact-row" style="top:218px">
    <svg width="22" height="22" viewBox="0 0 22 22"><circle cx="11" cy="11" r="11" fill="#fff"/><path d="M7 6c1 0 1.5 2 2 3l-1 1c.7 1.5 2 2.8 3.5 3.5l1-1c1 .5 3 1 3 2s-1 2-2 2C9 16.5 5.5 13 5.5 8c0-1 1-2 1.5-2z" fill="#0f1b28"/></svg>
    <span>(916) 555-0142</span>
  </div>
  <div class="contact-row" style="top:271px">
    <svg width="22" height="22" viewBox="0 0 22 22"><circle cx="11" cy="11" r="11" fill="#fff"/><rect x="5.5" y="7" width="11" height="8" fill="#0f1b28"/><path d="M5.5 7l5.5 4.5L16.5 7" stroke="#fff" stroke-width="1.2" fill="none"/></svg>
    <span>info@velotrin.com</span>
  </div>

  <div class="abs" style="left:111px;top:330px;width:980px;height:1px;background:#4a5866"></div>
  <p class="abs" style="left:0;top:344px;width:1200px;text-align:center;font-size:14px">© 2026 Velotrin Construction, Inc.</p>
</footer>
<span class="social" style="left:118px"></span>
<span class="social" style="left:153px"></span>
<span class="social" style="left:188px"></span>
<span class="social" style="left:224px"></span>

</body>
</html>
```